Business Card Design

We are looking for a business card designed for our landscaping company. We do landscaping installation & Maintenance Services. We would like to see designs that have basic landscaping in background. We also think it is important to have both of our names and phone numbers on the card. We need something that stands out a little whether it is shape of the card or thickness or design.

Business

Bramblewood Yardworks, bramblewoodyard@mailvista.net, Owen Platt 555-273-9104, Daniel Korbin 555-618-3927

```html
<!DOCTYPE html>
<html lang="en">
<head>
<meta charset="utf-8">
<title>Bramblewood Yardworks – Business Card</title>
<link href="https://fonts.googleapis.com/css2?family=Old+Standard+TT:wght@700&family=Arimo:wght@400&display=swap" rel="stylesheet">
<style>
  :root {
    --backdrop: #e9e7e3;
    --card-black: #141414;
    --card-edge: #1f1f1f;
    --brand-green: #1be03c;
    --ink-white: #f4f4f4;
  }
  html, body {
    margin: 0;
    padding: 0;
    width: 1200px;
    height: 780px;
    overflow: hidden;
    background: var(--backdrop);
  }
  .stage {
    width: 1200px;
    height: 780px;
    display: flex;
    align-items: center;
    justify-content: center;
  }
  .business-card {
    position: relative;
    width: 840px;
    height: 480px;
    background: var(--card-black);
    border: 1px solid var(--card-edge);
    border-radius: 6px;
    box-shadow: 0 10px 30px rgba(0,0,0,0.25);
    overflow: hidden;
  }
  .company-name {
    position: absolute;
    left: 52px;
    top: 58px;
    margin: 0;
    font-family: "Old Standard TT", Georgia, serif;
    font-weight: 700;
    font-size: 54px;
    letter-spacing: 0.5px;
    color: var(--brand-green);
    white-space: nowrap;
  }
  .title-rule {
    position: absolute;
    left: 34px;
    right: 40px;
    top: 142px;
    height: 2px;
    background: var(--brand-green);
  }
  .email {
    position: absolute;
    left: 88px;
    top: 168px;
    font-family: "Arimo", Arial, sans-serif;
    font-size: 25px;
    color: var(--ink-white);
  }
  .contact {
    position: absolute;
    color: var(--ink-white);
  }
  .contact-name {
    display: block;
    font-family: "Old Standard TT", Georgia, serif;
    font-weight: 700;
    font-size: 32px;
    line-height: 1.1;
  }
  .contact-phone {
    display: block;
    font-family: "Arimo", Arial, sans-serif;
    font-size: 24px;
    margin-top: 4px;
  }
  .contact-left { left: 62px; top: 262px; }
  .contact-right { left: 440px; top: 356px; }
  .contact-divider {
    position: absolute;
    left: 372px;
    top: 300px;
    width: 2px;
    height: 96px;
    background: var(--ink-white);
  }
</style>
</head>
<body>
  <main class="stage">
    <article class="business-card">
      <h1 class="company-name">Bramblewood Yardworks</h1>
      <div class="title-rule"></div>
      <div class="email">bramblewoodyard@mailvista.net</div>
      <div class="contact contact-left">
        <span class="contact-name">Owen Platt</span>
        <span class="contact-phone">555-273-9104</span>
      </div>
      <div class="contact-divider"></div>
      <div class="contact contact-right">
        <span class="contact-name">Daniel Korbin</span>
        <span class="contact-phone">555-618-3927</span>
      </div>
    </article>
  </main>
</body>
</html>
```